Gift Cards in the Mail Envelope

Mailing out gift cards in the envelope. Need an eye popping envelope. Please look at the enclosed images. The envelope should look like that.

Low design quality

```html
<!DOCTYPE html>
<html lang="en">
<head>
<meta charset="UTF-8">
<title>Envelope Design – Front and Back</title>
<link href="https://fonts.googleapis.com/css2?family=Lato:wght@400&display=swap" rel="stylesheet">
<style>
  :root {
    --navy: #08314d;
    --lime: #95c83a;
    --paper: #ffffff;
    --rule: #9a9a9a;
    --backdrop: #e6e6e6;
  }
  * { margin: 0; padding: 0; box-sizing: border-box; }
  html, body {
    width: 1200px;
    height: 1200px;
    overflow: hidden;
    background: var(--backdrop);
  }
  .canvas {
    position: relative;
    width: 1200px;
    height: 1200px;
  }
  .envelope {
    position: absolute;
    background: var(--paper);
    box-shadow: 0 2px 5px rgba(0, 0, 0, 0.25);
    overflow: hidden;
  }
  .envelope svg {
    position: absolute;
    inset: 0;
    width: 100%;
    height: 100%;
    display: block;
  }
  .envelope-front {
    left: 190px;
    top: 192px;
    width: 818px;
    height: 410px;
  }
  .envelope-back {
    left: 192px;
    top: 703px;
    width: 814px;
    height: 404px;
  }
  .return-address {
    position: absolute;
    left: 72px;
    top: 358px;
    font-family: "Lato", sans-serif;
    font-weight: 400;
    font-size: 15.5px;
    color: var(--paper);
    white-space: nowrap;
  }
</style>
</head>
<body>
<main class="canvas">

  <section class="envelope envelope-front" aria-label="Envelope front">
    <svg viewBox="0 0 1023 512" preserveAspectRatio="none" aria-hidden="true">
      <g class="address-rules" stroke="var(--rule)" stroke-width="2">
        <line x1="95" y1="75" x2="520" y2="75"/>
        <line x1="95" y1="135" x2="520" y2="135"/>
        <line x1="95" y1="195" x2="520" y2="195"/>
      </g>
      <path class="wave-accent" fill="var(--lime)"
        d="M0,392 C80,350 180,330 300,348 C450,372 650,438 820,460 C930,474 990,440 1023,402 L1023,512 L0,512 Z"/>
      <path class="wave-gap" fill="var(--paper)"
        d="M0,410 C80,368 180,352 300,368 C450,392 650,450 820,469 C930,481 990,452 1023,420 L1023,512 L0,512 Z"/>
      <path class="wave-band" fill="var(--navy)"
        d="M0,418 C80,377 180,362 300,377 C450,400 650,456 820,476 C930,488 990,462 1023,430 L1023,512 L0,512 Z"/>
    </svg>
    <p class="return-address">421, Address line goes here Country Name, 45452</p>
  </section>

  <section class="envelope envelope-back" aria-label="Envelope back">
    <svg viewBox="0 0 1018 505" preserveAspectRatio="none" aria-hidden="true">
      <polygon class="flap" fill="var(--navy)" points="0,0 1018,0 977,119 41,119"/>
    </svg>
  </section>

</main>
</body>
</html>
```